BOLD & MINIMALIST DESIGN NEEDED

We want a very bold but minimalistic business card design that is impactful and utilizes both sides of the business card. Our current logo is included for your use.

We want bold fonts and good use of negative space. We don't want the logo to overpower the design.

Target Market(s)

Professionals who are building new commercial buildings.

Industry/Entity Type

Construction

Contact Information for Business Card

Name, Title, email, office phone, cell phone, website

Font styles to use
Serif
Sans Serif

Requirements
Must have
• Bold design!

```html
<!DOCTYPE html>
<html lang="en">
<head>
<meta charset="utf-8">
<title>Norcrest Build – Business Card</title>
<link href="https://fonts.googleapis.com/css2?family=Oswald:wght@500;600&family=Montserrat:wght@400;600&display=swap" rel="stylesheet">
<style>
  :root {
    --page-bg: #1a1a1a;
    --card-white: #ffffff;
    --card-dark: #2b2b2b;
    --card-dark-light: #3a3a3a;
    --ink: #1c1c1c;
    --green: #7dc12b;
    --back-mark: #5a5a5a;
  }
  * { margin: 0; padding: 0; box-sizing: border-box; }
  html, body {
    width: 1200px; height: 897px; overflow: hidden;
    background: var(--page-bg);
    font-family: "Montserrat", sans-serif;
  }
  .card {
    position: absolute; left: 303px; width: 594px; height: 338px;
    border-radius: 18px; overflow: hidden;
  }
  .card--front { top: 92px; background: var(--card-white); color: var(--ink); }
  .card--back {
    top: 470px;
    background: linear-gradient(135deg, var(--card-dark) 0%, var(--card-dark-light) 100%);
    display: flex; align-items: center; justify-content: center;
  }
  .brand {
    position: absolute; left: 30px; top: 70px;
    display: flex; align-items: center; gap: 10px;
  }
  .brand__square { width: 22px; height: 22px; background: var(--green); }
  .brand__name {
    font-family: "Oswald", sans-serif; font-weight: 600;
    font-size: 30px; letter-spacing: 1px; color: var(--ink); line-height: 1;
  }
  .person__name {
    position: absolute; left: 30px; top: 192px;
    font-family: "Oswald", sans-serif; font-weight: 600;
    font-size: 32px; color: var(--green); line-height: 1; letter-spacing: 0.3px;
  }
  .person__title {
    position: absolute; left: 30px; top: 228px;
    font-size: 14px; letter-spacing: 0.5px;
  }
  .divider {
    position: absolute; left: 95px; top: 236px; width: 471px; height: 1.5px;
    background: var(--green);
  }
  .contacts { position: absolute; left: 30px; top: 258px; list-style: none; }
  .contacts li {
    display: flex; align-items: center; gap: 5px;
    font-size: 14px; height: 18.5px;
  }
  .contacts svg { width: 13px; height: 13px; fill: none; stroke: var(--green); stroke-width: 2; }
  .website {
    position: absolute; right: 29px; top: 294px;
    font-size: 14px; font-weight: 600; letter-spacing: 0.8px;
  }
  .website__domain { color: var(--green); font-weight: 400; }
  .accent-bar {
    position: absolute; left: 343px; bottom: 0; width: 221px; height: 9px;
    background: var(--green);
  }
  .back-name {
    font-family: "Oswald", sans-serif; font-weight: 600;
    font-size: 56px; letter-spacing: 4px; color: var(--back-mark);
  }
</style>
</head>
<body>
  <section class="card card--front">
    <div class="brand">
      <span class="brand__square"></span>
      <span class="brand__name">NORCREST BUILD</span>
    </div>

    <h1 class="person__name">MARCUS REED</h1>
    <p class="person__title">OWNER</p>
    <div class="divider"></div>

    <ul class="contacts">
      <li>
        <svg viewBox="0 0 24 24"><path d="M5 3h4l2 5-3 2a12 12 0 0 0 6 6l2-3 5 2v4a2 2 0 0 1-2 2A18 18 0 0 1 3 5a2 2 0 0 1 2-2z"/></svg>
        (555) 014-2290
      </li>
      <li>
        <svg viewBox="0 0 24 24"><path d="M3 9c5-4 13-4 18 0l-3 2-2-2H8l-2 2z"/><rect x="6" y="12" width="12" height="8" rx="1"/><circle cx="12" cy="16" r="1.5"/></svg>
        (555) 014-2290
      </li>
      <li>
        <svg viewBox="0 0 24 24"><rect x="3" y="6" width="18" height="12"/><path d="M3 6l9 7 9-7"/></svg>
        hello@norcrestbuild.com
      </li>
    </ul>

    <p class="website">www.<span class="website__domain">norcrestbuild</span>.com</p>
    <div class="accent-bar"></div>
  </section>

  <section class="card card--back">
    <span class="back-name">NORCREST</span>
  </section>
</body>
</html>
```